Web Design for Webdesign company 3 page PSD

Project
---------
We need a PSD Web Design to be used in a WordPress installation.
What we would like to create is a professional looking website for a web design agency. We also need you to look for suitable stock images to be placed on these pages.
We need the design for:
Homepage
Landing page
Contact page
attached in the pages file you will find a file with more in depth details how these files should be build up.
We would like to see a desktop version and a mobile version of these pages
The website should have a 1100px width.
The mobile design should have 480px width.
The homepage should have a header slider about 450px high.
The slider is preferred full width and should have some images text and a button
Objectives
-------------
The main objective for the website is to get leads from customers in the form of a request for a quotation or a call or mail me back action. The most important action for the homepage is to link and navigate to our landing pages.
What we want to tell our visitors (our main products)
-------------------------------------------------------------------
- A website with no big investment but a monthly rate
- A successful website with no worries (a complete website, seo, hosting and a service contract for future customization is included for a monthly rate)
Color Scheme
------------
Use branding colors. You can find them in the branding.pdf file.
Additional colors:
White: #ffffff
Black: #181818
Company info
--------------
We are a starting web design / marketing agency based in The Netherlands and looking for the design of our website. Our services are (custom) webdesign, website marketing or combinations of both. Our main customer group is small business owners.
We sell websites but give the option to buy it with a lease contract.
A second product is a default website with a complete service: SEO, hosting and a service contract for a monthly rate.
Content:
-----------
If not available place Lorem Ipsum text.
There will come about 400 words of text on the landing pages
Design Competition
--------------------------
Since this is a designing competition we would like to see your creativity.
What you can expect from us is a lot of feedback 7 days a week with short response time.
You can send us the first sketchy mock ups of the homepage and we will give feedback based on these design. But we like your feedback or comments as well
Read the pages file for more in depth details how the pages should be designed

Target Market(s)
Small business owners in The Netherlands
Industry/Entity Type
It Company
Number of Pages Required
3 page
Requirements
Must have
- Homepage:
- Header slider with images, some text and a link to a custom page
- The slider should have 3 designed slides
- Landings page:
- Sidebar
- Action button for a request for a quotation
- Action button for a call me back action
- Action button for an appointment
- Contact form:
- Address details
- Contact form
Nice to have
- Homepage:
- Full width slider
- Testimonial block
- Blog items
Should not have
- Flash
- A to crowded design

```html
<!DOCTYPE html>
<html lang="en">
<head>
<meta charset="utf-8">
<title>Brightline Web Agency</title>
<link href="https://fonts.googleapis.com/css2?family=Raleway:wght@400;500;600;700&family=Open+Sans:ital,wght@0,400;0,600;1,400&display=swap" rel="stylesheet">
<style>
:root{
  --green:#4f8a72;
  --green-dark:#3f7560;
  --hero-a:#6c9c8c;
  --hero-b:#3f6d60;
  --ink:#181818;
  --text:#333333;
  --muted:#8a8a8a;
  --white:#ffffff;
  --black-band:#0c0c0c;
  --grey-band:#f2f2f2;
  --footer:#2b2b2b;
  --line:#e2e2e2;
}
*{margin:0;padding:0;box-sizing:border-box}
html,body{width:734px;height:1200px;overflow:hidden;background:var(--white)}
body{position:relative;font-family:"Open Sans",Arial,sans-serif;color:var(--text)}
h1,h2,h3{font-weight:500}

/* header */
.site-header{position:absolute;left:0;top:0;width:734px;height:54px;background:var(--white)}
.brand{position:absolute;left:128px;top:14px;display:flex;align-items:center;gap:8px}
.brand-mark{width:22px;height:22px;background:var(--green)}
.brand-text{display:flex;flex-direction:column;gap:3px}
.brand-name{font-family:"Raleway",sans-serif;font-weight:600;font-size:12px;line-height:12px;color:var(--ink);letter-spacing:.3px}
.brand-tagline{font-family:"Raleway",sans-serif;font-weight:400;font-size:6.2px;line-height:7px;color:var(--muted)}
.main-nav{position:absolute;top:24px;left:0;width:734px;font-family:"Raleway",sans-serif;font-size:7.2px;color:#777;text-transform:uppercase}
.main-nav a{position:absolute;color:inherit;text-decoration:none;transform:translateX(-50%);white-space:nowrap}
.main-nav a.active{color:var(--green)}
.main-nav a.active::after{content:"";position:absolute;left:-2px;right:-2px;top:12px;height:2px;background:var(--green)}

/* hero */
.hero{position:absolute;left:0;top:54px;width:734px;height:302px;overflow:hidden}
.hero-photo{position:absolute;inset:0;background:linear-gradient(120deg,var(--hero-a),var(--hero-b) 55%,#557f73)}
.hero-title{position:absolute;top:33px;left:0;width:734px;text-align:center;font-family:"Raleway",sans-serif;font-weight:500;font-size:25px;letter-spacing:2.6px;color:var(--white)}
.hero-sub{position:absolute;top:64px;left:0;width:734px;text-align:center;font-family:"Raleway",sans-serif;font-weight:500;font-size:10.5px;letter-spacing:1.5px;color:var(--white)}
.hero-btn{position:absolute;left:331px;top:83px;width:76px;height:20px;background:var(--white);border-radius:2px;font-family:"Raleway",sans-serif;font-weight:600;font-size:6.8px;line-height:20px;text-align:center;color:var(--ink)}
.hero-devices{position:absolute;left:197px;top:114px;width:330px;height:180px;background:linear-gradient(180deg,#3a3f46,#24282d);border-radius:3px;opacity:.9}
.hero-arrow{position:absolute;top:120px}

/* services */
.service{position:absolute;top:386px;width:140px;text-align:center}
.service svg{display:block;margin:0 auto}
.service h3{margin-top:6px;font-family:"Raleway",sans-serif;font-weight:500;font-size:10.5px;color:var(--ink)}
.service p{margin-top:4px;font-size:5.4px;line-height:8px;color:var(--muted)}

/* about */
.about{position:absolute;left:0;top:518px;width:734px;height:213px;background:var(--black-band)}
.about h2{position:absolute;left:128px;top:45px;font-family:"Raleway",sans-serif;font-weight:500;font-size:15px;color:var(--white)}
.about p{position:absolute;left:128px;width:238px;font-size:5.6px;line-height:8.8px;color:var(--white)}
.about .p1{top:71px}
.about .p2{top:95px}
.btn-green{position:absolute;left:128px;top:141px;width:80px;height:21px;background:var(--green);font-family:"Raleway",sans-serif;font-weight:600;font-size:7px;line-height:21px;text-align:center;color:var(--white)}
.about-photo{position:absolute;left:396px;top:40px;width:209px;height:131px;background:linear-gradient(135deg,#c9d3d8,#8a9aa3 50%,#5f6b70);border:1px solid #ddd}

/* blog */
.blog-heading{position:absolute;left:128px;top:761px;font-family:"Raleway",sans-serif;font-weight:400;font-size:13px;color:var(--ink)}
.post{position:absolute;top:788px;width:148px}
.post-photo{width:148px;height:65px}
.post h3{margin-top:8px;font-family:"Raleway",sans-serif;font-weight:500;font-size:7.3px;color:var(--text)}
.post p{margin-top:3px;font-size:5.2px;line-height:8.6px;color:var(--muted)}
.post a{display:block;margin-top:5px;font-size:5.8px;color:#1e4f6c;text-decoration:none}

/* testimonials */
.testimonials{position:absolute;left:0;top:948px;width:734px;height:194px;background:var(--grey-band)}
.testimonials h2{position:absolute;left:0;width:724px;top:24px;text-align:center;font-family:"Raleway",sans-serif;font-weight:500;font-size:14px;color:var(--ink)}
.quote{position:absolute;top:55px;width:154px}
.quote-card{height:81px;background:var(--white);border:1px solid var(--line);padding:11px 10px 0;text-align:center;font-style:italic;font-size:5.4px;line-height:10px;color:#555}
.quote-avatar{position:absolute;left:60px;top:61px;width:34px;height:34px;border-radius:50%;background:linear-gradient(135deg,#d8c1ad,#9c7a62);border:2px solid var(--white)}
.quote cite{display:block;margin-top:16px;text-align:center;font-style:normal;font-size:5.8px;color:#444}

/* footer */
.site-footer{position:absolute;left:0;top:1142px;width:734px;height:58px;background:var(--footer)}
.footer-nav{position:absolute;left:128px;top:19px;font-family:"Raleway",sans-serif;font-weight:600;font-size:6.6px;color:var(--white)}
.footer-nav span{margin:0 3px;font-weight:400}
.copyright{position:absolute;left:128px;top:34px;font-size:5.6px;color:#ccc}
.social{position:absolute;left:548px;top:18px;display:flex;gap:6px}
.social i{display:block;width:9px;height:9px;border-radius:50%;background:var(--white)}
</style>
</head>
<body>

<header class="site-header">
  <div class="brand">
    <div class="brand-mark"></div>
    <div class="brand-text">
      <div class="brand-name">Brightline Web Agency</div>
      <div class="brand-tagline">Heldere sites voor ondernemers</div>
    </div>
  </div>
  <nav class="main-nav">
    <a class="active" style="left:370px">Home</a>
    <a style="left:418px">About Us</a>
    <a style="left:474px">Services</a>
    <a style="left:530px">Projects</a>
    <a style="left:585px">Contact</a>
  </nav>
</header>

<section class="hero">
  <div class="hero-photo" role="img" aria-label="Team of designers working together at a table, tinted green"></div>
  <h1 class="hero-title">RESPONSIVE WEB DESIGN</h1>
  <p class="hero-sub">YOUR WEBSITE READABLE ON ALL DEVICES</p>
  <div class="hero-btn">CALL TO ACTION</div>
  <div class="hero-devices" role="img" aria-label="Website shown on desktop, laptop, tablet and phone"></div>
  <svg class="hero-arrow" style="left:104px" width="20" height="44" viewBox="0 0 20 44"><polyline points="18,1 2,22 18,43" fill="none" stroke="#fff" stroke-width="1.5"/></svg>
  <svg class="hero-arrow" style="left:606px" width="20" height="44" viewBox="0 0 20 44"><polyline points="2,1 18,22 2,43" fill="none" stroke="#fff" stroke-width="1.5"/></svg>
</section>

<section class="services">
  <div class="service" style="left:146px">
    <svg width="56" height="62" viewBox="0 0 56 62"><polygon points="28,1 54,16 54,46 28,61 2,46 2,16" fill="#4f8a72"/>
      <rect x="18" y="25" width="20" height="14" rx="1.5" fill="#fff"/><rect x="24" y="21" width="8" height="5" rx="1" fill="none" stroke="#fff" stroke-width="2"/><rect x="18" y="30" width="20" height="1.5" fill="#4f8a72"/></svg>
    <h3>Web Development</h3>
    <p>acilisis massa Etiam eu urna Sed porta<br>Suspendisse quam leo molestie sed luctus quis<br>feugiat in pede Fusce tellus</p>
  </div>
  <div class="service" style="left:293px">
    <svg width="56" height="62" viewBox="0 0 56 62"><polygon points="28,1 54,16 54,46 28,61 2,46 2,16" fill="#4f8a72"/>
      <circle cx="22" cy="25" r="3.5" fill="#fff"/><circle cx="34" cy="25" r="3.5" fill="#fff"/><circle cx="28" cy="29" r="4" fill="#fff"/>
      <path d="M16 37 q6-8 12-1 q6-7 12 1 v2 h-24z" fill="#fff"/></svg>
    <h3>Web Designing</h3>
    <p>acilisis massa Etiam eu urna Sed porta<br>Suspendisse quam leo molestie sed luctus quis<br>feugiat in pede Fusce tellus</p>
  </div>
  <div class="service" style="left:441px">
    <svg width="56" height="62" viewBox="0 0 56 62"><polygon points="28,1 54,16 54,46 28,61 2,46 2,16" fill="#4f8a72"/>
      <circle cx="28" cy="31" r="7" fill="none" stroke="#fff" stroke-width="4" stroke-dasharray="3.5 2"/><circle cx="28" cy="31" r="5.5" fill="#fff"/><circle cx="28" cy="31" r="2.5" fill="#4f8a72"/></svg>
    <h3>Programming &amp; SEO</h3>
    <p>acilisis massa Etiam eu urna Sed porta<br>Suspendisse quam leo molestie sed luctus quis<br>feugiat in pede Fusce tellus</p>
  </div>
</section>

<section class="about">
  <h2>ABOUT OUR COMPANY</h2>
  <p class="p1">Curabitur iaculis tempus eros Curabitur vel mi sit amet magna malesuada ultrices Ut nisi erat fermentum vel congue id euismod in elit Fusce ultricies orci</p>
  <p class="p2">Morbi ornare gravida elit Integer congue augue et malesuada iaculis ipsum dui aliquet felis at cursus magna nisl nec elit Praesent elementum elit at tellus nec ultricies sit amet porttitor mattis enim In massa libero interdum nec interdum vel blandit sed nulla In ullamcorper est eget tempor cursus</p>
  <div class="btn-green">CALL TO ACTION</div>
  <div class="about-photo" role="img" aria-label="Colleagues smiling at a desk in a bright office"></div>
</section>

<h2 class="blog-heading">Latest Blog Post</h2>
<article class="post" style="left:128px">
  <div class="post-photo" role="img" aria-label="Tablet showing a team hiring page on a colourful desk" style="background:linear-gradient(135deg,#7fb6b8,#d9cfa8 60%,#c0574a)"></div>
  <h3>Ut nisi erat fermentum</h3>
  <p>Vivamus porttitor purus nisi eleifend libero a tempus libero lectus feugiat felis Morbi diam mauris viverra in gravida eu mattis in ante Morbi eget arcu Morbi porta</p>
  <a>Read More</a>
</article>
<article class="post" style="left:294px">
  <div class="post-photo" role="img" aria-label="Group of colleagues looking at a laptop" style="background:linear-gradient(135deg,#e9eef1,#b9c3c9 50%,#6e7478)"></div>
  <h3>Class aptent taciti sociosqu</h3>
  <p>Vivamus porttitor purus nisi eleifend libero a tempus libero lectus feugiat felis Morbi diam mauris viverra in gravida eu mattis in ante Morbi eget arcu Morbi porta</p>
  <a>Read More</a>
</article>
<article class="post" style="left:458px">
  <div class="post-photo" role="img" aria-label="Business team meeting in a modern office" style="background:linear-gradient(135deg,#5d6469,#a7b0b5 55%,#dfe4e6)"></div>
  <h3>Mauris vel lacus vitae felis</h3>
  <p>Vivamus porttitor purus nisi eleifend libero a tempus libero lectus feugiat felis Morbi diam mauris viverra in gravida eu mattis in ante Morbi eget arcu Morbi porta</p>
  <a>Read More</a>
</article>

<section class="testimonials">
  <h2>TESTIMONIALS</h2>
  <blockquote class="quote" style="left:126px">
    <div class="quote-card">Morbi diam mauris viverra in gravida eu mattis in ante Morbi eget arcu Morbi porta libero id ullam-corper nonummy nibh ligula pulvinar metus eget consectetuer augue nisi quis lacus Ut ac</div>
    <div class="quote-avatar" role="img" aria-label="Client portrait"></div>
    <cite>By Author Name, City Location</cite>
  </blockquote>
  <blockquote class="quote" style="left:287px">
    <div class="quote-card">Morbi diam mauris viverra in gravida eu mattis in ante Morbi eget arcu Morbi porta libero id ullam-corper nonummy nibh ligula pulvinar metus eget consectetuer augue nisi quis lacus Ut ac</div>
    <div class="quote-avatar" role="img" aria-label="Client portrait" style="background:linear-gradient(135deg,#6bc3c7,#6a4a3a)"></div>
    <cite>By Author Name, City Location</cite>
  </blockquote>
  <blockquote class="quote" style="left:448px">
    <div class="quote-card">Morbi diam mauris viverra in gravida eu mattis in ante Morbi eget arcu Morbi porta libero id ullam-corper nonummy nibh ligula pulvinar metus eget consectetuer augue nisi quis lacus Ut ac</div>
    <div class="quote-avatar" role="img" aria-label="Client portrait" style="background:linear-gradient(135deg,#dfe8ee,#e4c79a)"></div>
    <cite>By Author Name, City Location</cite>
  </blockquote>
</section>

<footer class="site-footer">
  <nav class="footer-nav">HOME<span>|</span>ABOUT US<span>|</span>SERVICES<span>|</span>PROJECTS<span>|</span>BLOG<span>|</span>CONTACT</nav>
  <p class="copyright">© 2015 Company Name &nbsp;All right reserved &nbsp;Term of Use</p>
  <div class="social" aria-label="Social links"><i></i><i></i><i></i><i></i></div>
</footer>

</body>
</html>
```